Velvet Riot Rising Line of Sparkling Wine & Spirits

Back info: Nora Beth Quill Owner 555-318-4402 1480 E. Harlow Ave, Bldg. 2, & 3, Lodi Ca. 95871
Sparkling Wines & Memorabilia www.velvetriotrising.com
Ok I have uploaded the winning design. The color that I am after is the Fushia, Raspberry, Red, Matte Satin Matalic Finish. With a 24 Karet Gold color Foil. The Bottle is on the top row and it's the 2nd Bottle in. That is the Color that I want. This is the style of font. Make sure that you put what we're advertising. Good Luck to you all. Warmest regards, Nora
21 & up UniSex
Sparkling Wine and Memorabilia
there listed up above.....

```html
<!DOCTYPE html>
<html lang="en">
<head>
<meta charset="utf-8">
<title>Velvet Riot Rising — Business Card</title>
<link href="https://fonts.googleapis.com/css2?family=Arimo:wght@400;700&display=swap" rel="stylesheet">
<style>
  :root {
    --bg: #e4e4e4;
    --card-top: #ffffff;
    --card-bottom: #6b6b6b;
    --fuchsia: #d1197a;
    --fuchsia-deep: #a40f5c;
    --fuchsia-light: #ec4aa0;
    --gold: #e0a83a;
    --bronze: #8a5520;
    --ink: #4a4a4a;
    --ink-dark: #111111;
  }
  * { margin: 0; padding: 0; box-sizing: border-box; }
  html, body {
    width: 1200px; height: 1200px; overflow: hidden;
    background: var(--bg);
    font-family: "Arimo", Arial, sans-serif;
  }
  .canvas { position: relative; width: 1200px; height: 1200px; }
  .card {
    position: absolute;
    width: 687px; height: 392px;
    background: linear-gradient(to bottom,
      var(--card-top) 0%, var(--card-top) 46%,
      #d6d6d6 58%, #9a9a9a 80%, var(--card-bottom) 100%);
    box-shadow: 0 18px 26px rgba(0,0,0,0.28);
  }
  .card--front { left: 267px; top: 159px; }
  .card--back  { left: 262px; top: 654px; }

  .edge-tab { position: absolute; width: 10px; border-radius: 0 4px 4px 0; }
  .edge-tab--pink { left: 0; top: 73px; height: 53px; background: linear-gradient(to right, var(--fuchsia-deep), var(--fuchsia)); }
  .edge-tab--bronze { right: 0; top: 75px; height: 114px; border-radius: 4px 0 0 4px; background: linear-gradient(to right, var(--bronze), #b07838); }
  .card--back .edge-tab--bronze { top: 75px; height: 112px; width: 3px; }

  .owner { position: absolute; left: 38px; top: 76px; }
  .owner__name { color: var(--fuchsia); font-weight: 700; font-size: 27px; letter-spacing: 0.3px; line-height: 1; }
  .owner__role { color: var(--gold); font-size: 17px; line-height: 1; margin-top: 3px; }

  .contact { position: absolute; right: 40px; top: 76px; text-align: right; color: var(--ink); font-size: 16px; line-height: 21px; }
  .contact__block + .contact__block { margin-top: 30px; }

  .bottle {
    position: absolute;
    border-radius: 16px 16px 12px 12px;
    background: linear-gradient(to right, var(--fuchsia-deep), var(--fuchsia-light) 45%, var(--fuchsia) 70%, var(--fuchsia-deep));
  }
  .card--front .bottle { left: 310px; top: 32px; width: 99px; height: 328px; }
  .card--back .bottle { left: 307px; top: 57px; width: 70px; height: 242px; }

  .horizon { position: absolute; left: 140px; top: 300px; width: 411px; height: 1px;
    background: linear-gradient(to right, transparent, #555 30%, #555 70%, transparent); }
  .tagline { position: absolute; left: 0; right: 0; top: 329px; text-align: center;
    font-size: 17px; letter-spacing: 4px; color: var(--ink-dark); }
  .tagline b { font-weight: 700; }
</style>
</head>
<body>
<div class="canvas">
  <section class="card card--front">
    <span class="edge-tab edge-tab--pink"></span>
    <span class="edge-tab edge-tab--bronze"></span>
    <div class="owner">
      <div class="owner__name">NORA BETH QUILL</div>
      <div class="owner__role">Owner</div>
    </div>
    <div class="bottle" role="img" aria-label="Fuchsia satin sparkling wine bottle with gold foil label"></div>
    <div class="contact">
      <div class="contact__block">E. Harlow Ave<br>Bldg. 2, &amp; 3, Lodi Ca. 95871</div>
      <div class="contact__block">555-318-4402 1480<br>www.velvetriotrising.com</div>
    </div>
  </section>

  <section class="card card--back">
    <span class="edge-tab edge-tab--bronze"></span>
    <div class="bottle" role="img" aria-label="Fuchsia satin sparkling wine bottle with gold foil label"></div>
    <div class="horizon"></div>
    <p class="tagline">SPARKLING <b>WINES &amp; MEMORABILIA</b></p>
  </section>
</div>
</body>
</html>
```